We need a business card for our gym. We are a PowerCore affiliate in Decatur Georgie established 2008. Our company name is Rally Functional Fitness. PowerCore Building Prime Fitness. Instagram and website is @rallygym. Hashtags we use #rallywithheart #madetorally We want something similar to the the black and neon green design attached but a different color scheme. No neon colors. Are company colors are the same as the blue and white card attached. We are open to ideas as far as colors however - just no neon.

Contact Information for Business Card

Rally Functional Fitness
472 Halvern Drive
Decatur GA 30041
Phone 404.555.0187 Website www.rallygym.example

Font styles to use
Other font styles liked:
• Futura Extra Bold Condensed

Colors

Designer to choose colors to be used in the design.

Requirements
Must have
• Our primary font we typically use for our name is Futura Extra Bold Condensed
Nice to have
• I attached a card from that is black and neon green from Zorva that we would like something similar. The blue and white is more similar to our colors. We also use have used black and white in the past. We use the chevrons as out logo. We are a PowerCore affiliate so I included a logo from them as well that may or may not be used on the card. Our instagram is @rallygym hashtags #madetorally #rallywithheart
Should not have
• No neon colors

```html
<!DOCTYPE html>
<html lang="en">
<head>
<meta charset="utf-8">
<title>Rally Functional Fitness – Business Card</title>
<link rel="stylesheet" href="https://fonts.googleapis.com/css2?family=Anton&family=Oswald:wght@500&family=Montserrat:wght@400;500&display=swap">
<style>
  :root {
    --backdrop: #2a2b2d;
    --card: #1d1e20;
    --card-back-top: #2b2c2f;
    --card-back-bottom: #1a1b1d;
    --brand-blue: #2fb3e6;
    --white: #ffffff;
    --rule: #8a8c90;
  }
  * { box-sizing: border-box; margin: 0; padding: 0; }
  html, body {
    width: 1200px;
    height: 1108px;
    overflow: hidden;
    background: var(--backdrop);
  }
  .stage {
    position: relative;
    width: 1200px;
    height: 1108px;
  }
  .card {
    position: absolute;
    top: 244px;
    width: 380px;
    height: 620px;
    border-radius: 24px;
    overflow: hidden;
    box-shadow: 0 18px 40px rgba(0,0,0,0.45);
  }
  .card--front {
    left: 150px;
    background: var(--card);
    text-align: center;
    color: var(--white);
  }
  .card--back { left: 670px; }

  .brand {
    margin-top: 96px;
    font-family: "Anton", "Arial Narrow", sans-serif;
    color: var(--brand-blue);
    text-transform: uppercase;
    line-height: 0.95;
  }
  .brand__name { display: block; font-size: 84px; letter-spacing: 1px; }
  .brand__tagline { display: block; font-size: 24px; letter-spacing: 1px; }

  .person { margin-top: 118px; }
  .person__name {
    font-family: "Oswald", "Arial Narrow", sans-serif;
    font-weight: 500;
    font-size: 34px;
    color: var(--brand-blue);
    text-transform: uppercase;
    letter-spacing: 0.5px;
    line-height: 1.1;
  }
  .person__role {
    font-family: "Montserrat", sans-serif;
    font-size: 17px;
    letter-spacing: 1.5px;
    text-transform: uppercase;
  }

  .divider {
    display: flex;
    align-items: center;
    justify-content: center;
    gap: 8px;
    margin: 12px 40px 10px;
  }
  .divider__line { flex: 1; height: 1px; background: var(--rule); }
  .divider__icons { display: flex; gap: 5px; }

  .contact, .address {
    font-family: "Montserrat", sans-serif;
    font-size: 18px;
    line-height: 1.4;
  }
  .rule {
    height: 1px;
    background: var(--rule);
    margin: 14px 60px;
  }

  .back-pattern {
    position: absolute;
    inset: 0;
    background: linear-gradient(160deg, var(--card-back-top), var(--card-back-bottom));
  }
  .back-mark {
    position: absolute;
    right: 52px;
    bottom: 150px;
    font-family: "Anton", "Arial Narrow", sans-serif;
    font-size: 40px;
    color: var(--brand-blue);
    text-transform: uppercase;
    letter-spacing: 1px;
  }
</style>
</head>
<body>
<main class="stage">
  <section class="card card--front" aria-label="Card front">
    <h1 class="brand">
      <span class="brand__name">Rally</span>
      <span class="brand__tagline">Functional Fitness</span>
    </h1>

    <div class="person">
      <p class="person__name">Marcus Ellery</p>
      <p class="person__role">Expert Coaches</p>
    </div>

    <div class="divider">
      <span class="divider__line"></span>
      <span class="divider__icons">
        <svg width="24" height="24" viewBox="0 0 24 24" aria-label="Phone">
          <circle cx="12" cy="12" r="12" fill="var(--brand-blue)"/>
          <path d="M8 6.5l2 0 1 3-1.5 1a7 7 0 0 0 4 4l1-1.5 3 1v2a1.5 1.5 0 0 1-1.5 1.5A10 10 0 0 1 6.5 8 1.5 1.5 0 0 1 8 6.5z" fill="var(--card)"/>
        </svg>
        <svg width="24" height="24" viewBox="0 0 24 24" aria-label="Email">
          <circle cx="12" cy="12" r="12" fill="var(--brand-blue)"/>
          <rect x="6" y="8" width="12" height="8" rx="1" fill="var(--card)"/>
          <path d="M6.5 8.5l5.5 4 5.5-4" stroke="var(--brand-blue)" stroke-width="1.2" fill="none"/>
        </svg>
        <svg width="24" height="24" viewBox="0 0 24 24" aria-label="Website">
          <circle cx="12" cy="12" r="12" fill="var(--brand-blue)"/>
          <circle cx="12" cy="12" r="6" fill="none" stroke="var(--card)" stroke-width="1.6"/>
          <ellipse cx="12" cy="12" rx="2.6" ry="6" fill="none" stroke="var(--card)" stroke-width="1.3"/>
          <path d="M6 12h12" stroke="var(--card)" stroke-width="1.3"/>
        </svg>
      </span>
      <span class="divider__line"></span>
    </div>

    <p class="contact">
      404.555.0187<br>
      info@rallygym.example<br>
      www.rallygym.example
    </p>
    <div class="rule"></div>
    <p class="address">
      472 Halvern Drive<br>
      Decatur GA 30041
    </p>
  </section>

  <section class="card card--back" aria-label="Card back">
    <div class="back-pattern" role="img" aria-label="Tonal dark grey repeating pattern filling the card back"></div>
    <p class="back-mark">Rally</p>
  </section>
</main>
</body>
</html>
```